Real Estate Company Looking for Business Card Designs for 3 Executives

Hello!
Thanks so much for considering our project! We are a real estate investment company located in Edmonton, Alberta called Bellhaven Group of Companies. We invest/develop both commercial and residential real estate and are looking to create 3 DOUBLE-SIDED business cards for 3 top executives in the company! (for some reason it won't let us select the double-sided option, but yes, the cards are double sided and would be happy to tip extra)

We have certain guidelines that we want our business cards to for sure follow - the back of the Business card has to be the Black Background Version of the Logo which has already been designed and linked as a file (first file). We want the entire back of the card to simply just be the black background logo. In terms of the front of the card, would like to see a smaller version of the white background logo (linked as the second file) in the top left hand corner - of course, feel free to get creative and we can make revisions together along the way! and Then after that, just text. We want the card to be sharp, clean, easy on the eyes and highly professional looking. We would like the card to include the Full name of the Company (Bellhaven Group of Companies), Name of the Person, Title, Phone, Email. If possible please provide the front part of the card for 3 people:

1) Bellhaven Group of Companies, Liora Quenby, Chief Financial Officer, 780-555-0142, lioraquenby@bellhavengroup.example

2) Bellhaven Group of Companies, Tobias Quenby, Chief Executive Officer, 780-555-0187, tobiasquenby@bellhavengroup.example

3) Bellhaven Group of Companies, Rui Delcourt, Chief Operations Officer, 587-555-0163, ruidelcourt@bellhavengroup.example

Thank you so much for considering our project & we look forward to seeing your designs!

```html
<!DOCTYPE html>
<html lang="en">
<head>
<meta charset="utf-8">
<title>Bellhaven Group of Companies — Business Card</title>
<link href="https://fonts.googleapis.com/css2?family=Arimo:wght@400;700&family=Josefin+Sans:wght@400&display=swap" rel="stylesheet">
<style>
  :root {
    --backdrop: #e4e4e2;
    --card-white: #ffffff;
    --card-black: #2f2f2f;
    --ink: #2b2b2b;
    --ink-soft: #3a3a3a;
    --tree-dark: #262626;
    --tree-emboss-top: #4a4a4a;
    --tree-emboss-bottom: #1c1c1c;
    --paper-white: #ffffff;
  }
  * { box-sizing: border-box; margin: 0; padding: 0; }
  html, body {
    width: 1200px;
    height: 801px;
    overflow: hidden;
    background: var(--backdrop);
  }
  .canvas {
    position: relative;
    width: 1200px;
    height: 801px;
    display: flex;
    align-items: center;
    justify-content: center;
    gap: 50px;
  }
  .card {
    position: relative;
    width: 525px;
    height: 300px;
    overflow: hidden;
    box-shadow: 0 6px 18px rgba(0,0,0,0.12);
  }
  .card--front { background: var(--card-white); color: var(--ink); }
  .card--back  { background: var(--card-black); color: var(--paper-white); }

  .tree-art {
    position: absolute;
    top: 0;
    right: 0;
    height: 100%;
  }
  .card--front .tree-art {
    width: 160px;
    background: linear-gradient(90deg, rgba(38,38,38,0) 0%, var(--tree-dark) 45%, var(--tree-dark) 100%);
    opacity: 0.9;
  }
  .card--back .tree-art {
    width: 200px;
    background: linear-gradient(180deg, var(--tree-emboss-top) 0%, #2a2a2a 45%, var(--tree-emboss-bottom) 100%);
  }

  .wordmark {
    display: flex;
    align-items: center;
    gap: 10px;
    font-family: "Josefin Sans", sans-serif;
    font-weight: 400;
    white-space: nowrap;
  }
  .wordmark__square {
    width: 12px;
    height: 12px;
    flex: none;
    background: currentColor;
  }
  .card--front .wordmark {
    position: absolute;
    left: 34px;
    top: 46px;
    font-size: 17px;
    letter-spacing: 0.42em;
    color: var(--ink);
  }
  .card--back .wordmark {
    position: absolute;
    left: 46px;
    top: 134px;
    font-size: 21px;
    letter-spacing: 0.36em;
    color: var(--paper-white);
  }

  .company {
    position: absolute;
    left: 34px;
    top: 76px;
    font-family: "Arimo", sans-serif;
    font-size: 10px;
    letter-spacing: 0.12em;
    text-transform: uppercase;
    color: var(--ink-soft);
  }
  .person {
    position: absolute;
    left: 34px;
    top: 150px;
    font-family: "Arimo", sans-serif;
  }
  .person__name {
    font-size: 19px;
    font-weight: 700;
    text-transform: uppercase;
    letter-spacing: 0.02em;
    color: var(--ink);
  }
  .person__title {
    font-size: 14px;
    font-weight: 400;
    color: var(--ink-soft);
    margin-top: 2px;
  }
  .contact {
    position: absolute;
    left: 34px;
    top: 222px;
    list-style: none;
    font-family: "Arimo", sans-serif;
    font-size: 13.5px;
    color: var(--ink);
  }
  .contact__item {
    display: flex;
    align-items: center;
    gap: 9px;
    line-height: 22px;
    white-space: nowrap;
  }
  .contact__icon { width: 12px; height: 12px; flex: none; }
</style>
</head>
<body>
<main class="canvas">

  <section class="card card--front" aria-label="Front of business card">
    <div class="tree-art" role="img" aria-label="Dark silhouette illustration of tall pine trunks with bare branches"></div>

    <div class="wordmark"><span class="wordmark__square"></span><span>BELLHAVEN</span></div>
    <p class="company">Bellhaven Group of Companies</p>

    <div class="person">
      <p class="person__name">Liora Quenby</p>
      <p class="person__title">Chief Financial Officer</p>
    </div>

    <ul class="contact">
      <li class="contact__item">
        <svg class="contact__icon" viewBox="0 0 24 24" aria-hidden="true">
          <path fill="currentColor" d="M6.6 10.8a15.1 15.1 0 0 0 6.6 6.6l2.2-2.2a1 1 0 0 1 1-.25 11.4 11.4 0 0 0 3.6.57 1 1 0 0 1 1 1V20a1 1 0 0 1-1 1A17 17 0 0 1 3 4a1 1 0 0 1 1-1h3.5a1 1 0 0 1 1 1c0 1.25.2 2.45.57 3.57a1 1 0 0 1-.25 1z"/>
        </svg>
        <span>780-555-0142</span>
      </li>
      <li class="contact__item">
        <svg class="contact__icon" viewBox="0 0 24 24" aria-hidden="true">
          <rect x="2.5" y="5" width="19" height="14" rx="1.5" fill="none" stroke="currentColor" stroke-width="2"/>
          <path d="M3 6l9 7 9-7" fill="none" stroke="currentColor" stroke-width="2"/>
        </svg>
        <span>lioraquenby@bellhavengroup.example</span>
      </li>
    </ul>
  </section>

  <section class="card card--back" aria-label="Back of business card">
    <div class="tree-art" role="img" aria-label="Embossed dark illustration of pine trunks with bare branches"></div>
    <div class="wordmark"><span class="wordmark__square"></span><span>BELLHAVEN</span></div>
  </section>

</main>
</body>
</html>
```